German Headhunter/ HR Consultancy needs Business Cards Design

We need a business Card Design for our Company in Stuttgart. We are specialized as Headhunter/ HR Consultancy in Placement of specialist and managers in permanent employment. Please refer to our business logo.

```html
<!DOCTYPE html>
<html lang="de">
<head>
<meta charset="utf-8">
<title>Kernwerk Personalberatung – Visitenkarte</title>
<link href="https://fonts.googleapis.com/css2?family=Montserrat:wght@500;700&family=Arimo:wght@400&display=swap" rel="stylesheet">
<style>
  :root{
    --bg:#2b2b2b;
    --card-white:#ffffff;
    --card-black:#1a1a1a;
    --brand-blue:#2f4aa0;
    --text-grey:#6b6b6b;
    --rule-grey:#b5b5b5;
    --mark-dark:#3a3a3a;
  }
  *{margin:0;padding:0;box-sizing:border-box}
  html,body{width:1200px;height:1040px;overflow:hidden;background:var(--bg)}
  .canvas{width:1200px;height:1040px;display:flex;flex-direction:column;align-items:center;justify-content:center;gap:60px}
  .card{width:760px;height:434px;border-radius:0 90px 0 90px;position:relative;overflow:hidden}
  .card--back{background:var(--card-black);display:flex;align-items:center;justify-content:center}
  .back-mark{font-family:"Montserrat",sans-serif;font-weight:700;font-size:46px;letter-spacing:4px;color:var(--mark-dark);text-transform:uppercase}
  .card--front{background:var(--card-white);display:flex;align-items:center}
  .brand{width:50%;display:flex;align-items:center;justify-content:center;gap:16px}
  .brand-square{width:46px;height:46px;background:var(--brand-blue)}
  .brand-name{font-family:"Montserrat",sans-serif;font-weight:700;font-size:22px;line-height:1.15;color:var(--brand-blue);text-transform:uppercase;letter-spacing:1px}
  .divider{width:1px;height:230px;background:var(--rule-grey)}
  .details{padding-left:34px}
  .person-name{font-family:"Montserrat",sans-serif;font-weight:700;font-size:27px;color:var(--brand-blue);text-transform:uppercase;letter-spacing:1px}
  .person-role{font-family:"Arimo",sans-serif;font-size:17px;color:var(--text-grey);text-transform:uppercase;letter-spacing:1px;margin-bottom:16px}
  .contact-list{list-style:none}
  .contact-item{display:flex;align-items:center;gap:10px;font-family:"Arimo",sans-serif;font-size:19px;color:var(--text-grey);line-height:1.55;letter-spacing:.5px}
  .contact-icon{width:18px;height:18px;flex:none;fill:var(--brand-blue)}
  .address{font-family:"Arimo",sans-serif;font-size:19px;color:var(--text-grey);line-height:1.4;margin-top:12px;letter-spacing:.5px}
</style>
</head>
<body>
<main class="canvas">
  <section class="card card--back" aria-label="Rückseite">
    <span class="back-mark">Kernwerk</span>
  </section>

  <section class="card card--front" aria-label="Vorderseite">
    <div class="brand">
      <span class="brand-square"></span>
      <span class="brand-name">Kernwerk<br>Personalberatung</span>
    </div>
    <div class="divider"></div>
    <div class="details">
      <h1 class="person-name">Lukas Brenner</h1>
      <p class="person-role">Managing Director</p>
      <ul class="contact-list">
        <li class="contact-item">
          <svg class="contact-icon" viewBox="0 0 24 24"><path d="M6.6 10.8a15 15 0 0 0 6.6 6.6l2.2-2.2c.3-.3.7-.4 1-.2 1.1.4 2.3.6 3.6.6.6 0 1 .4 1 1V20c0 .6-.4 1-1 1A17 17 0 0 1 3 4c0-.6.4-1 1-1h3.5c.6 0 1 .4 1 1 0 1.3.2 2.5.6 3.6.1.3 0 .7-.2 1z"/></svg>
          0711-555 018 42
        </li>
        <li class="contact-item">
          <svg class="contact-icon" viewBox="0 0 24 24"><path d="M2 5h20v14H2z" fill="none"/><path d="M2 5h20l-10 7z"/><path d="M2 7l10 7 10-7v12H2z"/></svg>
          kontakt@kernwerk-hr.de
        </li>
        <li class="contact-item">
          <svg class="contact-icon" viewBox="0 0 24 24"><circle cx="12" cy="12" r="9.5" fill="none" stroke="#2f4aa0" stroke-width="2"/><ellipse cx="12" cy="12" rx="4" ry="9.5" fill="none" stroke="#2f4aa0" stroke-width="1.6"/><path d="M2.5 12h19M4 7h16M4 17h16" stroke="#2f4aa0" stroke-width="1.4"/></svg>
          www.kernwerk-hr.de
        </li>
      </ul>
      <p class="address">18, Lindenweg 4b<br>70173, Stuttgart</p>
    </div>
  </section>
</main>
</body>
</html>
```